Boundless Volt Product design

We need a bottle design for our product. Boundless Volt is a Gaming Nootropic made to increase Energy, Focus, Reaction time, and Clarity of an eSport gamer. It will be 40 servings a bottle. Currently, all the ingredients haven't been finalized so after the competition is over we will have to work with the designer to also make an ingredients label for the back of it. For the flavor, we will call it tundra mist.

The attachments included:. The velvet outlaws picture as a font style I like for the logo.
The Z CHARGE REFRESH PICTURE IS WHAT WE WANT OUR DESIGN to look like something similar a clean and simple design that stands out!

Z Charge bottle is what our biggest competitors product looks like. The boundless volt picture as the current logo we are using but can be changed.

Overall the pictures are just some references for what I could possibly want the design to look like however, I'm open to your designer's ideas and concepts you think would make for a cool looking Gaming Nootropic product bottle design. I appreciate everyone working on this and look forward to seeing your designs have a great day!

Target Market(s)

Gamers between the ages of 18-30

Industry/Entity Type

Health And Wellness

Requirements
Must have
• Boundless Volt logo, state that it is for energy, focus, reaction, and clarity. state 40 serivngs. state flavor.

```html
<!DOCTYPE html>
<html lang="en">
<head>
<meta charset="utf-8">
<title>Boundless Volt — Tundra Mist Label</title>
<link href="https://fonts.googleapis.com/css2?family=Exo+2:wght@500;600&family=Saira+Condensed:ital,wght@0,700;1,700;1,800&family=Roboto:wght@400&display=swap" rel="stylesheet">
<style>
  :root {
    --navy: #1d3f99;
    --band-blue: #2a55a8;
    --band-blue-light: #3a6cc0;
    --tab-blue: #2f52a8;
    --tab-blue-light: #3d62b8;
    --teal: #5ccbd5;
    --ink: #0f2560;
    --sky: #a9cdf0;
    --white: #ffffff;
    --mist: #eef2f8;
  }
  * { margin: 0; padding: 0; box-sizing: border-box; }
  html, body { width: 1200px; height: 334px; overflow: hidden; background: var(--white); }

  .label {
    position: relative;
    width: 1200px;
    height: 334px;
    overflow: hidden;
    background: linear-gradient(180deg, var(--white) 0%, var(--white) 40%, var(--mist) 65%);
    font-family: "Saira Condensed", sans-serif;
  }

  .top-stripes {
    position: absolute; left: 0; top: 0; width: 1200px; height: 45px;
    background: linear-gradient(180deg, var(--sky) 0%, #d3e6f8 100%);
    opacity: 0.75;
  }

  .servings-tab {
    position: absolute; left: 734px; top: 0; width: 50px; height: 148px;
    border-radius: 0 0 10px 10px;
    background: linear-gradient(160deg, var(--tab-blue-light), var(--tab-blue));
    color: var(--white); text-align: center;
  }
  .servings-count {
    position: absolute; left: 0; right: 0; top: 98px;
    font-size: 26px; font-weight: 700; line-height: 1;
  }
  .servings-word {
    position: absolute; left: 0; right: 0; top: 127px;
    font-size: 11px; font-weight: 700; line-height: 1;
  }

  .brand {
    position: absolute; left: 424px; top: 96px; width: 300px;
    display: flex; align-items: center; justify-content: center; gap: 10px;
  }
  .brand-mark { width: 14px; height: 14px; background: var(--teal); }
  .brand-name {
    font-family: "Exo 2", sans-serif; font-weight: 600;
    font-size: 30px; color: var(--ink); letter-spacing: 0.5px; line-height: 1;
  }

  .audience {
    position: absolute; left: 448px; top: 160px; width: 240px; text-align: center;
    font-style: italic; font-weight: 800; font-size: 21px;
    letter-spacing: 3.2px; color: var(--navy); line-height: 1;
  }

  .bottom-band {
    position: absolute; left: 0; top: 218px; width: 1200px; height: 116px;
    background: linear-gradient(180deg, var(--band-blue-light) 0%, var(--band-blue) 55%, var(--band-blue) 100%);
  }

  .zero-badges { position: absolute; left: 428px; top: 220px; }

  .flavor {
    position: absolute; left: 612px; top: 221px;
    font-style: italic; font-weight: 700; font-size: 23px;
    letter-spacing: 1.6px; color: var(--white); line-height: 1;
  }

  .benefits {
    position: absolute; left: 0; right: 0; top: 264px; text-align: center;
    font-weight: 700; font-size: 20px; letter-spacing: 2.6px;
    color: var(--white); line-height: 1;
  }

  .legal {
    position: absolute; left: 0; right: 0; top: 289px; text-align: center;
    font-family: "Roboto", sans-serif; font-size: 10.5px;
    color: #d9e3f5; letter-spacing: 0.3px;
  }
</style>
</head>
<body>
  <main class="label">
    <div class="top-stripes" role="img" aria-label="Light blue dashed stripe band"></div>

    <div class="servings-tab">
      <span class="servings-count">40</span>
      <span class="servings-word">servings</span>
    </div>

    <div class="brand">
      <span class="brand-mark"></span>
      <span class="brand-name">BOUNDLESS VOLT</span>
    </div>

    <p class="audience">FOR E-SPORT GAMERS</p>

    <section class="bottom-band">
    </section>

    <svg class="zero-badges" width="182" height="30" viewBox="0 0 182 30" aria-label="0 sugar, 0 calories, 0 caffeine">
      <g fill="#ffffff">
        <polygon points="3,2 44,2 41,26 0,26"/>
        <polygon points="47,2 88,2 85,26 44,26"/>
        <polygon points="91,2 132,2 129,14 182,14 176,26 88,26"/>
      </g>
      <g fill="#1d3f99" font-family="Saira Condensed, sans-serif" font-style="italic" font-weight="800" text-anchor="middle">
        <text x="23" y="19" font-size="20">0</text>
        <text x="67" y="19" font-size="20">0</text>
        <text x="111" y="19" font-size="20">0</text>
        <text x="21" y="25" font-size="5">SUGAR</text>
        <text x="65" y="25" font-size="5">CALORIES</text>
        <text x="109" y="25" font-size="5">CAFFEINE</text>
      </g>
    </svg>

    <p class="flavor">TUNDRA MIST</p>

    <p class="benefits">ENERGY | FOCUS | REACTION | CLARITY</p>
    <p class="legal">Dietary Supplement | Net Weight 12 OZ (118g)</p>
  </main>
</body>
</html>
```